Simple and Clean business card design

We would like the design to be simple clean and to incorporate our colors.

We are open to your design and talent, we have the dots in our logo as we think of it as data points and we connect data points for people.

We are open to see the great creative and clean design you bring to the table

Contact Information for Business Card

please include: name, position, email, phone and website

Font styles to use
Sans Serif

Requirements
Must have
• my colors incorporated, simplicity
Nice to have
• lots of white space, simplicity
Should not have
• complexicity/ complex art

```html
<!DOCTYPE html>
<html lang="en">
<head>
<meta charset="utf-8">
<title>Quilla Business Card</title>
<link href="https://fonts.googleapis.com/css2?family=Lato:wght@400;700;900&display=swap" rel="stylesheet">
<style>
  :root {
    --bg: #a6d3d2;
    --paper: #f5f5f5;
    --lavender: #e2e1ef;
    --ink: #1f2120;
    --dark: #232424;
    --orange: #e8731f;
    --brand-blue: #4a74c9;
    --white: #ffffff;
  }
  * { margin: 0; padding: 0; box-sizing: border-box; }
  html, body { width: 1200px; height: 1200px; overflow: hidden; }
  body {
    background: var(--bg);
    font-family: "Lato", Arial, sans-serif;
    position: relative;
  }
  .card {
    position: absolute;
    left: 160px;
    width: 880px;
    height: 503px;
    background: var(--paper);
    overflow: hidden;
    box-shadow: 0 10px 30px rgba(0,0,0,0.18);
  }
  .card-front { top: 70px; }
  .card-back { top: 627px; }
  .card-shapes { position: absolute; inset: 0; width: 100%; height: 100%; }

  .brand {
    position: absolute;
    display: flex;
    align-items: center;
    gap: 16px;
    color: var(--ink);
    font-weight: 900;
    letter-spacing: -1px;
  }
  .brand-dot {
    width: 48px; height: 48px;
    border-radius: 50%;
    background: var(--brand-blue);
    flex: none;
  }
  .card-front .brand { left: 70px; top: 200px; font-size: 86px; }
  .card-back .brand { left: 0; right: 0; top: 40px; justify-content: center; font-size: 100px; }

  .contact {
    position: absolute;
    left: 560px;
    top: 80px;
    width: 290px;
    color: var(--white);
  }
  .contact-name { font-size: 30px; font-weight: 900; letter-spacing: 0.5px; }
  .contact-role { font-size: 17px; font-weight: 400; letter-spacing: 0.5px; margin-top: 2px; }
  .contact-rule { width: 150px; height: 4px; background: var(--orange); margin: 18px 0 26px; }
  .contact-list { list-style: none; }
  .contact-item {
    display: flex;
    align-items: center;
    gap: 16px;
    margin-bottom: 22px;
    font-size: 16px;
    line-height: 1.3;
  }
  .contact-item.phone { font-size: 24px; }
  .contact-icon {
    width: 36px; height: 36px;
    border-radius: 50%;
    background: var(--orange);
    flex: none;
    display: flex; align-items: center; justify-content: center;
  }
  .contact-icon svg { width: 18px; height: 18px; }

  .back-website {
    position: absolute;
    left: 0; right: 0;
    top: 380px;
    text-align: center;
    color: var(--white);
    font-size: 28px;
    letter-spacing: 0.5px;
  }
</style>
</head>
<body>

<section class="card card-front">
  <svg class="card-shapes" viewBox="0 0 880 503" preserveAspectRatio="none" aria-hidden="true">
    <path d="M0 0 L360 0 Q500 190 520 503 L0 503 Z" fill="var(--lavender)"/>
    <path d="M385 0 L880 0 L880 503 L545 503 Q530 190 385 0 Z" fill="var(--dark)"/>
  </svg>

  <div class="brand"><span class="brand-dot"></span>Quilla</div>

  <div class="contact">
    <div class="contact-name">DANIEL REYES</div>
    <div class="contact-role">FOUNDER/ CEO</div>
    <div class="contact-rule"></div>
    <ul class="contact-list">
      <li class="contact-item phone">
        <span class="contact-icon">
          <svg viewBox="0 0 24 24" fill="#fff"><path d="M6.6 10.8a15.5 15.5 0 0 0 6.6 6.6l2.2-2.2a1 1 0 0 1 1-.25 11.4 11.4 0 0 0 3.6.57 1 1 0 0 1 1 1V20a1 1 0 0 1-1 1A17 17 0 0 1 3 4a1 1 0 0 1 1-1h3.5a1 1 0 0 1 1 1c0 1.25.2 2.45.57 3.6a1 1 0 0 1-.25 1z"/></svg>
        </span>
        555-214-3086
      </li>
      <li class="contact-item">
        <span class="contact-icon">
          <svg viewBox="0 0 24 24" fill="none" stroke="#fff" stroke-width="2"><rect x="3" y="5" width="18" height="14"/><path d="M3 5l9 8 9-8"/></svg>
        </span>
        <span>daniel.reyes@quilla.io<br>www.Quilla.io</span>
      </li>
      <li class="contact-item">
        <span class="contact-icon">
          <svg viewBox="0 0 24 24" fill="#fff"><path d="M12 2a7 7 0 0 0-7 7c0 5 7 13 7 13s7-8 7-13a7 7 0 0 0-7-7zm0 9.5A2.5 2.5 0 1 1 12 6.5a2.5 2.5 0 0 1 0 5z"/></svg>
        </span>
        <span>88 Orchard Lane,<br>Fairview, USA 402 17</span>
      </li>
    </ul>
  </div>
</section>

<section class="card card-back">
  <svg class="card-shapes" viewBox="0 0 880 503" preserveAspectRatio="none" aria-hidden="true">
    <path d="M0 330 Q380 170 880 200 L880 503 L0 503 Z" fill="var(--dark)"/>
  </svg>
  <div class="brand"><span class="brand-dot"></span>Quilla</div>
  <div class="back-website">www.Quilla.io</div>
</section>

</body>
</html>
```